KLV Plant Services

We are a heavy diesel mechanical business with additional air con certificates, remapping engine rebuilt

Contact Information for Business Card

Company Name, Director Name, Managing Director, Contact details, email and website

Font styles to use
Serif
Script

```html
<!DOCTYPE html>
<html lang="en">
<head>
<meta charset="utf-8">
<title>KLV Plant Services – Business Cards</title>
<link rel="stylesheet" href="https://fonts.googleapis.com/css2?family=Marcellus&display=swap">
<style>
  :root {
    --backdrop: #3a3a3c;
    --card: #ffffff;
    --card-shade: #eeeeef;
    --navy: #28236e;
    --rule: #4b4190;
    --ink: #111111;
    --muted: #555555;
  }
  * { margin: 0; padding: 0; box-sizing: border-box; }
  html, body {
    width: 1200px; height: 900px; overflow: hidden;
    background: var(--backdrop);
    font-family: "Marcellus", serif;
  }
  .canvas { position: relative; width: 1200px; height: 900px; }
  .card {
    position: absolute;
    width: 560px; height: 320px;
    background: linear-gradient(135deg, var(--card) 40%, var(--card-shade));
    box-shadow: 0 12px 28px rgba(0,0,0,.45);
  }
  .card--services { left: 80px; top: 90px; }
  .card--contact { left: 560px; top: 500px; }

  .brand {
    display: flex; align-items: center; gap: 10px;
    color: var(--navy);
    font-size: 30px; line-height: 1;
    white-space: nowrap;
  }
  .brand__mark {
    width: 30px; height: 30px; border-radius: 50%;
    border: 3px solid var(--navy);
  }
  .card--services .brand { position: absolute; top: 46px; left: 50%; transform: translateX(-50%); }
  .services__title {
    position: absolute; top: 120px; width: 100%;
    text-align: center; font-size: 19px; letter-spacing: .5px; color: var(--ink);
  }
  .services__list {
    position: absolute; top: 156px; width: 100%;
    list-style: none; text-align: center;
    font-size: 13.5px; line-height: 22px; color: var(--muted);
  }

  .card--contact .brand { position: absolute; top: 60px; right: 40px; }
  .contact__rule {
    position: absolute; left: 250px; right: 30px; top: 190px;
    height: 1px; background: var(--rule);
  }
  .contact__address {
    position: absolute; right: 30px; top: 120px;
    text-align: right; font-size: 14px; line-height: 20px; color: var(--muted);
  }
  .contact__person { position: absolute; left: 34px; top: 170px; }
  .contact__name { font-size: 20px; color: var(--ink); letter-spacing: .5px; }
  .contact__role { font-size: 15px; color: var(--navy); margin-top: 2px; }
  .contact__lines {
    position: absolute; left: 34px; top: 230px;
    list-style: none; font-size: 15px; line-height: 26px; color: var(--muted);
  }
  .contact__lines li { display: flex; align-items: center; gap: 10px; }
  .contact__icon { width: 14px; height: 14px; fill: none; stroke: var(--navy); stroke-width: 1.6; }
</style>
</head>
<body>
<main class="canvas">

  <section class="card card--services">
    <div class="brand"><span class="brand__mark"></span>KLV Plant Services</div>
    <h2 class="services__title">OUR SERVICES</h2>
    <ul class="services__list">
      <li>Civil And Mining Equipment Repair And Maintenance</li>
      <li>Mobile And Fixed Plant Services / Component Rebuilds</li>
      <li>Crushing Equipment Repair / Road Transport Maintenance / Diagnostics</li>
      <li>Ecu Remapping / Auto Electrics / Air Conditioning</li>
      <li>Fabrication And Boiler Making / Labour Hire / Specialised Tool Hire</li>
    </ul>
  </section>

  <section class="card card--contact">
    <div class="brand"><span class="brand__mark"></span>KLV Plant Services</div>
    <address class="contact__address">
      48 Ridgeway Drive<br>Marlow Heights<br>WA 6099, Australia
    </address>
    <div class="contact__rule"></div>
    <div class="contact__person">
      <div class="contact__name">ROSS HALE</div>
      <div class="contact__role">Managing Director</div>
    </div>
    <ul class="contact__lines">
      <li>
        <svg class="contact__icon" viewBox="0 0 16 16" aria-hidden="true"><path d="M3 1.5l3 3-1.5 2a8 8 0 0 0 5 5l2-1.5 3 3-2 2C6 15 1 10 1 3.5z"/></svg>
        0400 555 219
      </li>
      <li>
        <svg class="contact__icon" viewBox="0 0 16 16" aria-hidden="true"><rect x="1" y="3" width="14" height="10"/><path d="M1 3l7 6 7-6"/></svg>
        admin@klvplantservices.net
      </li>
      <li>
        <svg class="contact__icon" viewBox="0 0 16 16" aria-hidden="true"><circle cx="8" cy="8" r="6.5"/><ellipse cx="8" cy="8" rx="3" ry="6.5"/><path d="M1.5 8h13"/></svg>
        www.klvplantservices.net
      </li>
    </ul>
  </section>

</main>
</body>
</html>
```